Liron Vasek Website

Website for my son who is in 7th grade in the US. This will prepare him to show people his accomplishments when applying for a job or going to college. It should have:
* A picture (or multiple pictures)
* A resume page
* A place to share your accomplishments
* Links to his other social profiles
* A contact form

Great to include:
* Internships (show some photos of it along with what you’ve learned).
* Volunteer work.
* A side hustle that you want to highlight

Website sample I like:
https://belinamorud.sitefolio-demo.com/belinamorudtavik

Target Market(s)

For jobs and colleges admissions.

Number of Pages Required

5+ page

Colors

Designer to choose colors to be used in the design.

Requirements
Must have
• * A picture (or multiple pictures)
• * A resume page
• * A place to share your accomplishments
• * Links to his other social profiles
• * A contact form
Nice to have
• Great to include:
• * Internships (show some photos of it along with what you’ve learned).
• * Volunteer work.
• * A side hustle that you want to highlight

```html
<!DOCTYPE html>
<html lang="en">
<head>
<meta charset="utf-8">
<title>Liron Vasek</title>
<link href="https://fonts.googleapis.com/css2?family=Poppins:wght@300;400;500;600&family=Open+Sans:wght@400&display=swap" rel="stylesheet">
<style>
:root{
  --blue:#0b74d4;
  --ink:#1d1d1d;
  --muted:#555;
  --white:#fff;
  --dark:#1f2730;
  --field:#e6e6e6;
}
*{margin:0;padding:0;box-sizing:border-box}
html,body{width:1200px;height:3339px;overflow:hidden;background:var(--white);font-family:'Poppins',sans-serif;color:var(--ink)}
.page{position:relative;width:1200px;height:3339px}
.abs{position:absolute}
/* header */
.call{left:115px;top:24px;display:flex;align-items:center;gap:10px}
.call-label{font-size:15px;font-weight:600;color:var(--blue);line-height:1.2}
.call-num{font-size:17px;color:var(--ink)}
.brand{left:0;width:1200px;top:22px;text-align:center;font-size:36px;font-weight:500;color:var(--blue)}
.brand span{color:var(--ink)}
.search{left:835px;top:24px;width:250px;height:44px;border:1px solid #ddd;border-radius:22px;font-size:14px;color:#888;padding:12px 16px}
.search-btn{position:absolute;right:5px;top:6px;width:32px;height:32px;border-radius:50%;background:var(--blue)}
.nav{left:0;width:1200px;top:104px;display:flex;justify-content:center;gap:31px;font-size:17px;font-weight:500}
.nav .socials{display:flex;gap:16px;align-items:center;margin-left:12px}
.dot{width:14px;height:14px;border-radius:50%;background:var(--ink);display:inline-block}
/* hero */
.hero{left:0;top:148px;width:1200px;height:675px;background:linear-gradient(180deg,#5a4a3a 0%,#7a6650 40%,#4f5760 75%,#3f464c 100%)}
.hero-title{left:92px;top:336px;font-size:53px;font-weight:600;color:var(--white)}
.hero-title b{color:var(--blue);font-weight:600}
.hero-sub{left:92px;top:406px;width:580px;font-size:23px;line-height:45px;color:var(--white)}
.btn{background:var(--blue);color:var(--white);border-radius:30px;font-weight:500;display:flex;align-items:center;justify-content:center;gap:10px}
.hero-btn{left:92px;top:511px;width:206px;height:54px;font-size:18px}
.btn i{width:17px;height:17px;border-radius:50%;background:var(--white);display:inline-block}
/* about */
.portrait{left:80px;top:935px;width:420px;height:420px;border-radius:50%;background:radial-gradient(circle at 50% 40%,#cfcfcf,#9a9a9a)}
.about-title{left:560px;top:962px;font-size:38px;font-weight:400}
.about-title b{color:var(--blue);font-weight:600}
.about-text{left:560px;top:1022px;width:550px;font-family:'Open Sans',sans-serif;font-size:16px;line-height:36px;text-align:justify;color:#333}
.about-btn{left:560px;top:1264px;width:206px;height:56px;font-size:18px}
/* highlights */
.dark{left:0;top:1460px;width:1200px;height:765px;background:linear-gradient(180deg,#2a3440,#1f2831 60%,#2b3034)}
.card{top:1662px;width:329px}
.card-img{height:193px}
.card h3{margin-top:16px;font-size:18px;font-weight:400;color:var(--blue)}
.card p{margin-top:6px;font-size:13px;line-height:25px;color:var(--white)}
.card a{display:block;margin-top:2px;font-size:18px;color:var(--white)}
/* contact info */
.h2{left:0;width:1200px;text-align:center;font-size:36px;font-weight:400;color:var(--blue)}
.sub{left:0;width:1200px;top:2368px;text-align:center;font-size:21px;color:var(--muted)}
.info{top:2430px;width:340px;text-align:center;font-size:19px;line-height:29px;color:var(--muted)}
.info .ic{width:84px;height:84px;border-radius:50%;background:var(--blue);margin:0 auto 14px;display:flex;align-items:center;justify-content:center}
.info b{color:var(--blue);font-weight:500;display:block}
/* form */
.field{height:42px;border:1px solid #eee;box-shadow:inset 0 3px 4px var(--field);font-size:12px;color:#555;padding:14px 18px}
.submit{left:511px;top:2925px;width:178px;height:49px;background:var(--blue);color:var(--white);font-size:17px;font-weight:600;display:flex;align-items:center;justify-content:center;gap:10px}
/* footer */
.footer{left:0;top:3075px;width:1200px;height:264px;background:var(--blue);color:var(--white);text-align:center}
.foot-name{margin-top:68px;font-size:42px}
.foot-social{margin-top:8px;display:flex;justify-content:center;gap:6px}
.foot-social span{width:30px;height:30px;border:1.5px solid var(--white);border-radius:50%}
.foot-nav{margin-top:14px;font-size:19px;font-weight:500}
.copy{margin-top:14px;font-size:15px}
.code{position:absolute;right:10px;bottom:12px;font-size:14px}
</style>
</head>
<body>
<div class="page">

<header>
  <div class="abs call">
    <svg width="42" height="42" viewBox="0 0 42 42"><circle cx="21" cy="21" r="19" fill="none" stroke="#0b74d4" stroke-width="2.5"/><path d="M14 12c2-1 3 0 4 3s-1 3-1 4c1 3 3 5 6 6 1 0 2-2 4-1s4 2 3 4-3 3-6 2c-6-2-10-7-12-12-1-3 0-5 2-6z" fill="#0b74d4"/></svg>
    <div><div class="call-label">CALL US:</div><div class="call-num">(555) 014-2290</div></div>
  </div>
  <div class="abs brand">LIRON <span>VASEK</span></div>
  <div class="abs search">Search<span class="search-btn"></span></div>
  <nav class="abs nav">
    <span>HOME</span><span>PORTFOLIO</span><span>RESUME</span><span>ACHIEVEMENTS</span><span>BLOG</span><span>CONTACT</span>
    <span class="socials"><i class="dot"></i><i class="dot"></i><i class="dot"></i><i class="dot"></i></span>
  </nav>
</header>

<section>
  <div class="abs hero" role="img" aria-label="Photo of a busy city avenue lined with tall office towers"></div>
  <svg class="abs" style="left:0;top:700px" width="1200" height="125" viewBox="0 0 1200 125">
    <path d="M0 123 Q600 -20 1200 123 L1200 125 L0 125Z" fill="#fff"/>
    <path d="M115 108 Q600 0 1085 108" fill="none" stroke="#0b74d4" stroke-width="6"/>
    <circle cx="600" cy="55" r="30" fill="#fff"/>
    <rect x="588" y="37" width="24" height="36" rx="12" fill="none" stroke="#222" stroke-width="2"/>
    <line x1="600" y1="43" x2="600" y2="52" stroke="#222" stroke-width="2"/>
  </svg>
  <h1 class="abs hero-title"><b>LIRON</b> VASEK</h1>
  <p class="abs hero-sub">Sed ut perspiciatis unde omnis iste natus error sit voluptatem accusantium doloremque.</p>
  <div class="abs btn hero-btn">CONTACT US <i></i></div>
</section>

<section>
  <svg class="abs" style="left:66px;top:920px" width="460" height="450" viewBox="0 0 460 450">
    <path d="M10 230 A220 220 0 1 1 230 450" fill="none" stroke="#0b74d4" stroke-width="7"/>
  </svg>
  <div class="abs portrait" role="img" aria-label="Portrait photo of Liron Vasek"></div>
  <h2 class="abs about-title"><b>ABOUT</b> ME</h2>
  <p class="abs about-text">Sed ut perspiciatis unde omnis iste natus error sit voluptatem accusantium doloremque laudantium, totam rem aperiam, eaque ipsa quae ab illo inventore veritatis et quasi architecto beatae vitae dicta sunt explicabo. Nemo enim ipsam voluptatem quia voluptas sit aspernatur aut odit aut fugit, sed quia consequuntur magni dolores eos qui ratione voluptatem sequi nesciunt.</p>
  <div class="abs btn about-btn">Read More <i></i></div>
</section>

<section>
  <div class="abs dark" role="img" aria-label="Dimmed aerial photo of a downtown skyline"></div>
  <svg class="abs" style="left:0;top:1455px" width="1200" height="100" viewBox="0 0 1200 100">
    <path d="M0 0 L1200 0 L1200 6 Q600 150 0 6Z" fill="#fff"/>
    <path d="M115 20 Q600 105 1085 20" fill="none" stroke="#0b74d4" stroke-width="7"/>
  </svg>
  <svg class="abs" style="left:0;top:2125px" width="1200" height="102" viewBox="0 0 1200 102">
    <path d="M0 98 Q600 -40 1200 98 L1200 102 L0 102Z" fill="#fff"/>
    <path d="M115 82 Q600 -8 1085 82" fill="none" stroke="#0b74d4" stroke-width="7"/>
  </svg>
  <article class="abs card" style="left:89px">
    <div class="card-img" role="img" aria-label="Photo of trophies lined up on a table" style="background:linear-gradient(135deg,#3f8a3c,#b89a3a,#6a5a8a)"></div>
    <h3>ACCOMPLISHMENTS</h3>
    <p>Sed ut perspiciatis unde omnis iste natus error sit voluptatem accusantium doloremque totam rem aperiam,</p>
    <a>Read more</a>
  </article>
  <article class="abs card" style="left:435px">
    <div class="card-img" role="img" aria-label="Illustrated photo about an internship" style="background:linear-gradient(135deg,#f1ece4,#d9d4cc)"></div>
    <h3>INTERNSHIPS</h3>
    <p>Sed ut perspiciatis unde omnis iste natus error sit voluptatem accusantium doloremque totam rem aperiam,</p>
    <a>Read more</a>
  </article>
  <article class="abs card" style="left:782px">
    <div class="card-img" role="img" aria-label="Photo of volunteers holding seedlings together" style="background:linear-gradient(135deg,#4f90bf,#5a6c5a,#3f6a8c)"></div>
    <h3>VOLUNTEER WORK</h3>
    <p>Sed ut perspiciatis unde omnis iste natus error sit voluptatem accusantium doloremque totam rem aperiam,</p>
    <a>Read more</a>
  </article>
</section>

<section>
  <h2 class="abs h2" style="top:2310px">CONTACT INFORMATION</h2>
  <p class="abs sub">Contact us for more information</p>
  <div class="abs info" style="left:123px">
    <div class="ic"><svg width="44" height="44" viewBox="0 0 44 44" fill="none" stroke="#fff" stroke-width="2"><path d="M22 36C14 26 12 22 12 17a10 10 0 0 1 20 0c0 5-2 9-10 19z"/><circle cx="22" cy="17" r="4"/><path d="M12 34h20"/></svg></div>
    14 Ashcombe Lane, Bramfield,<br>Hollowshire, HB72QN
  </div>
  <div class="abs info" style="left:431px">
    <div class="ic"><svg width="44" height="44" viewBox="0 0 44 44" fill="none" stroke="#fff" stroke-width="2"><path d="M13 9c3-2 4 0 6 4s-1 4-1 5c1 4 4 7 8 9 1 0 2-3 5-1s5 3 3 6-4 4-8 2c-7-3-13-9-15-16-1-4 0-7 2-9z"/></svg></div>
    <b>Phone:</b>555 014 2290
  </div>
  <div class="abs info" style="left:748px">
    <div class="ic"><svg width="48" height="36" viewBox="0 0 48 36" fill="none" stroke="#fff" stroke-width="2"><rect x="3" y="4" width="42" height="28"/><path d="M3 4l21 17 21-17M3 32l16-14M45 32L29 18"/></svg></div>
    <b>Email:</b>hello@lironvasek.com
  </div>

  <h2 class="abs h2" style="top:2636px">CONTACT US</h2>
  <form>
    <div class="abs field" style="left:161px;top:2706px;width:431px">First Name</div>
    <div class="abs field" style="left:610px;top:2706px;width:430px">Last Name</div>
    <div class="abs field" style="left:161px;top:2762px;width:431px">Company</div>
    <div class="abs field" style="left:610px;top:2762px;width:430px;height:151px">Message :</div>
    <div class="abs field" style="left:161px;top:2817px;width:431px">Email Address</div>
    <div class="abs field" style="left:161px;top:2871px;width:431px">Phone Number</div>
    <div class="abs submit"><svg width="18" height="16" viewBox="0 0 18 16"><path d="M0 7L18 0 14 16 9 11 15 3 7 10Z" fill="#fff"/></svg>SUBMIT</div>
  </form>
</section>

<footer class="abs footer">
  <div class="foot-name">LIRON VASEK</div>
  <div class="foot-social"><span></span><span></span><span></span><span></span></div>
  <div class="foot-nav">HOME &nbsp;|&nbsp; PORTFOLIO &nbsp;|&nbsp; RESUME &nbsp;|&nbsp; ACHIEVEMENTS &nbsp;|&nbsp; BLOG &nbsp;|&nbsp; CONTACT</div>
  <div class="copy">© 2019 Liron Vasek. All right reserved</div>
</footer>

</div>
</body>
</html>
```